Hop Along Days campaign: promoting kids play in the UK - Website Redesign

Hop Along Days is a national UK campaign that promotes the value of play for children. The current website is live at http://www.hopalongdays.co.uk. This website has been live for 4 years and now needs to be redesigned. The target audience is parents of young children up to the age of 12.

The current site was designed with a series of old adverts in mind. Here is an example of an old advert: http://vidshare.example/qR7tLm2XwZa

Criticisms of existing site:
The design represented the adverts too closely. The result was a website that mirrors the adverts rather than complements them.
The color scheme is too dark.
Text-heavy pages (e.g. http://www.hopalongdays.co.uk/fun.php) are dull and not FUN!

New site
We have recently had a series of new video adverts produced:
advert 1: http://vidshare.example/hB4nVc8JsPe
advert 2: http://vidshare.example/KgW3rTy9DuM
advert 3: http://vidshare.example/zA5oEi1HbNq

The new site should be cleaner and brighter than the existing site, possibly with a white background using graphics, fonts and advert characters (see attached character graphics files) to add the element of fun and play.

The homepage should include:
1. Hop Along Days logo (attached)
2. Social Media links (visible on all pages of the site) – Chatterbook, Chirpline, ClipVault
3. Link to the HopAlongDays app page of the site (visible on all pages)
4. Image/video placeholder that the user can scroll through, view full-size images and play videos.
5. Text area to hold approximately 100 words describing the purpose of the campaign
6. Site footer to contain the same information as on the existing site along with the Northern Games & Crafts Guild logo (attached)

Site structure:
One change to the site structure… the “Brought to you by” menu item will be removed from the top-level menu.

General:
Some pages on the existing site are quite text-heavy, we would like to break up text on these pages in some way. Graphical division of paragraphs, use of advert characters?

Please note that all attached graphics file are the property of the Northern Games & Crafts Guild and must only be used for the purpose of this project.

```html
<!DOCTYPE html>
<html lang="en">
<head>
<meta charset="utf-8">
<title>Hop Along Days – Home</title>
<link rel="stylesheet" href="https://fonts.googleapis.com/css2?family=Fredoka:wght@500;600&family=Open+Sans:wght@400;600;700&display=swap">
<style>
:root{
  --ink:#3b3b3b;
  --muted:#6d6d6d;
  --purple:#5a3f8c;
  --orange:#f29a1f;
  --red:#e2463b;
  --band-green:#eef6df;
  --band-blue:#e3f0fa;
  --band-pink:#fbe6ec;
  --card:#f4f1ea;
  --footer:#fbfaf6;
  --dark:#2a2a2a;
  --white:#ffffff;
}
*{box-sizing:border-box;margin:0;padding:0}
html,body{width:1200px;height:2196px;overflow:hidden}
body{background:var(--white);font-family:"Open Sans",Arial,sans-serif;color:var(--ink);font-size:13px;line-height:1.55;position:relative}
.wrap{width:900px;margin:0 auto;position:relative}
h2{font-family:"Fredoka",Arial,sans-serif;font-weight:600;text-align:center;color:#333;font-size:40px;line-height:1.1}
.read-more{color:var(--red);font-weight:700;font-size:12px;text-decoration:none}

/* header */
.site-header{position:absolute;left:0;right:0;top:0;height:150px}
.brand{position:absolute;left:150px;top:24px;display:flex;align-items:center;gap:10px;font-family:"Fredoka",Arial,sans-serif;font-weight:600;font-size:30px;color:var(--purple)}
.brand i{width:34px;height:34px;border-radius:50%;background:var(--orange);display:block}
.header-side{position:absolute;right:150px;top:14px;text-align:right}
.social{display:flex;gap:6px;justify-content:flex-end;margin-bottom:6px}
.social a{width:26px;height:26px;border-radius:4px;display:block}
.social .chatterbook{background:#3b5a9a}.social .chirpline{background:#2aa9e0}.social .clipvault{background:#d33a2c}
.contact{font-size:12px;color:var(--muted)}
.contact b{color:var(--purple)}
.main-nav{position:absolute;left:150px;right:150px;top:112px;height:34px;background:var(--purple);display:flex;border-radius:3px}
.main-nav a{flex:1;text-align:center;line-height:34px;color:var(--white);font-family:"Fredoka",Arial,sans-serif;font-size:16px;text-decoration:none}
.main-nav a.play{background:var(--orange);border-radius:3px 0 0 3px}

/* hero */
.hero{position:absolute;left:150px;top:150px;width:900px;height:410px;background:linear-gradient(165deg,#a9dcf2 0%,#c7e7c4 50%,#8cc456 100%)}
.hero-caption{position:absolute;left:0;right:0;bottom:0;height:42px;background:rgba(60,40,20,.75);color:#fff;font-family:"Fredoka",Arial,sans-serif;font-size:20px;line-height:42px;padding-left:18px}
.dots{position:absolute;right:16px;bottom:16px;display:flex;gap:5px}
.dots span{width:9px;height:9px;border-radius:50%;background:#fff;opacity:.6}
.dots span:first-child{opacity:1}

/* diamond */
.diamond{position:absolute;top:580px;left:0;right:0}
.diamond .sub{text-align:center;color:var(--muted);font-size:13px;margin-top:6px}
.cards{display:flex;gap:12px;justify-content:center;margin-top:34px;position:relative;z-index:2}
.card{width:152px;height:210px;background:var(--card);border-radius:4px;text-align:center;padding:16px 12px}
.card .icon{width:36px;height:36px;border-radius:50%;background:#4d4d68;margin:0 auto 10px}
.card h3{font-size:11px;font-weight:700;line-height:1.3;color:#333;margin-bottom:8px;text-transform:uppercase}
.card p{font-size:10.5px;color:var(--muted);line-height:1.5}
.card.active{background:var(--orange)}
.card.active h3,.card.active p{color:#fff}
.card.active .icon{background:#fff}
.arrow{position:absolute;top:90px;width:24px;height:24px;border-radius:50%;background:#fff;border:1px solid #ccc}
.arrow svg{display:block;margin:6px auto 0}

/* bands */
.band{position:absolute;left:0;right:0}
.about{top:960px;height:380px;background:var(--band-green)}
.videos{top:1340px;height:335px;background:var(--band-blue)}
.purpose{top:1675px;height:285px;background:var(--band-pink)}
.band h2{padding-top:40px}
.about h2{padding-top:50px}
.about-row{display:flex;gap:24px;margin-top:26px}
.video-frame{width:420px;height:230px;background:linear-gradient(135deg,#3e3450,#9b6a7b);flex:none;position:relative}
.video-frame .play{position:absolute;left:50%;top:50%;width:54px;height:38px;margin:-19px 0 0 -27px;background:rgba(0,0,0,.55);border-radius:8px}
.video-frame .play svg{display:block;margin:10px auto}
.about-text p{font-size:11.5px;color:var(--muted);margin-bottom:8px}
.thumbs{display:flex;gap:26px;justify-content:center;margin-top:26px;position:relative}
.thumb{width:210px;text-align:center}
.thumb .shot{height:140px;border:5px solid #fff;box-shadow:0 1px 3px rgba(0,0,0,.2)}
.thumb .t1{background:linear-gradient(135deg,#f3c08a,#c9856a)}
.thumb .t2{background:linear-gradient(135deg,#7fbf5c,#d9c46b)}
.thumb .t3{background:linear-gradient(135deg,#9ec7e8,#e3a86b)}
.thumb p{font-size:12px;color:var(--muted);margin-top:8px;line-height:1.3}
.purpose h2{padding-top:28px}
.purpose-row{display:flex;gap:30px;margin-top:16px}
.purpose-row p{font-size:11.5px;color:var(--muted);width:580px}
.purpose-photo{width:290px;height:180px;background:linear-gradient(135deg,#e9c9a8,#b88a6a);flex:none;margin-top:-20px}

/* footer */
.site-footer{position:absolute;top:1960px;left:0;right:0;height:236px;background:var(--footer)}
.app{position:absolute;left:150px;top:24px;width:150px}
.app h4{background:var(--red);color:#fff;font-family:"Fredoka",Arial,sans-serif;font-size:17px;text-align:center;padding:5px 0;border-radius:3px}
.store{display:flex;flex-direction:column;justify-content:center;height:42px;background:var(--dark);border-radius:5px;margin-top:8px;padding-left:14px;color:#fff;text-decoration:none}
.store small{font-size:8.5px;line-height:1.1;text-transform:uppercase;letter-spacing:.5px;color:#ddd}
.store strong{font-size:14px;line-height:1.2;font-weight:700;text-transform:uppercase}
.guild{position:absolute;left:410px;top:50px;width:380px;text-align:center}
.guild .name{font-family:"Fredoka",Arial,sans-serif;font-weight:600;font-size:22px;color:var(--purple);display:flex;align-items:center;justify-content:center;gap:10px}
.guild .name i{width:28px;height:28px;background:var(--orange);display:block}
.guild p{font-size:11px;color:var(--muted);margin-top:10px;line-height:1.6}
.footer-art{position:absolute;right:150px;top:24px;width:180px;height:150px;background:linear-gradient(135deg,#f3d27a,#9ccf6d)}
</style>
</head>
<body>

<header class="site-header">
  <div class="brand"><i></i>Hop Along Days</div>
  <div class="header-side">
    <div class="social">
      <a class="chatterbook" href="#" aria-label="Chatterbook"></a>
      <a class="chirpline" href="#" aria-label="Chirpline"></a>
      <a class="clipvault" href="#" aria-label="ClipVault"></a>
    </div>
    <div class="contact"><b>Call:</b> 0113 496 0217</div>
    <div class="contact"><b>Email:</b> hello@hopalongdays.co.uk</div>
  </div>
  <nav class="main-nav">
    <a class="play" href="#">Play right now</a>
    <a href="#">Get Involved</a>
    <a href="#">Why Play</a>
    <a href="#">Fun Corner</a>
    <a href="#">Resources</a>
    <a href="#">Contact Us</a>
  </nav>
</header>

<section class="hero" role="img" aria-label="Illustrated scene of cartoon children playing outside a treehouse on a green hill">
  <div class="hero-caption">We Enter to Learn, Leave to Achieve</div>
  <div class="dots"><span></span><span></span><span></span><span></span></div>
</section>

<section class="diamond">
  <h2>A child is an uncut Diamond</h2>
  <p class="sub">Advertising package that is specifically designed to meet your needs</p>
  <div class="wrap cards">
    <div class="arrow" style="left:-14px"><svg width="10" height="12"><path d="M7 1 2 6l5 5" stroke="#888" stroke-width="2" fill="none"/></svg></div>
    <div class="card"><div class="icon"></div><h3>Treasure<br>Hunt</h3><p>Fun trails to follow, find and share with friends in the park.</p></div>
    <div class="card"><div class="icon"></div><h3>Expand<br>our mind</h3><p>New games that spark big ideas and help little minds grow.</p></div>
    <div class="card active"><div class="icon"></div><h3>Learn<br>about risk</h3><p>Safe ways to climb, jump and try new things at every age.</p></div>
    <div class="card"><div class="icon"></div><h3>Play<br>together</h3><p>Simple games for the whole family to enjoy side by side.</p></div>
    <div class="card"><div class="icon"></div><h3>Learn<br>to share</h3><p>Take turns, swap toys and find joy in playing as a team.</p></div>
    <div class="arrow" style="right:-14px"><svg width="10" height="12"><path d="M3 1l5 5-5 5" stroke="#888" stroke-width="2" fill="none"/></svg></div>
  </div>
</section>

<section class="band about">
  <div class="wrap">
    <h2>Few words about HopAlongDays</h2>
    <div class="about-row">
      <div class="video-frame" role="img" aria-label="Video still from a campaign advert">
        <div class="play"><svg width="16" height="18"><path d="M2 1l13 8-13 8z" fill="#fff"/></svg></div>
      </div>
      <div class="about-text">
        <p>Hop Along Days is a national campaign that reminds parents how much children gain from play. We share ideas, games and simple tips for every day of the week.</p>
        <p>Play helps children learn, grow strong and make friends. It builds confidence, teaches them to solve problems and shows them how to manage small risks. Our new adverts follow families as they find time to play at home, in the garden and out in the park. Join in, try a new game and tell us what your family enjoyed most this week.</p>
        <a class="read-more" href="#">Read More »</a>
      </div>
    </div>
  </div>
</section>

<section class="band videos">
  <div class="wrap">
    <h2>View Play Videos</h2>
    <div class="thumbs">
      <div class="arrow" style="left:-14px;top:58px"><svg width="10" height="12"><path d="M7 1 2 6l5 5" stroke="#888" stroke-width="2" fill="none"/></svg></div>
      <div class="thumb"><div class="shot t1" role="img" aria-label="Video still of a child playing indoors"></div><p>How do I go go?<br><a class="read-more" href="#">Read More »</a></p></div>
      <div class="thumb"><div class="shot t2" role="img" aria-label="Video still of children exploring outdoors"></div><p>Explore the World.<br><a class="read-more" href="#">Read More »</a></p></div>
      <div class="thumb"><div class="shot t3" role="img" aria-label="Video still of a child climbing"></div><p>Learn about risks.<br><a class="read-more" href="#">Read More »</a></p></div>
      <div class="arrow" style="right:-14px;top:58px"><svg width="10" height="12"><path d="M3 1l5 5-5 5" stroke="#888" stroke-width="2" fill="none"/></svg></div>
    </div>
  </div>
</section>

<section class="band purpose">
  <div class="wrap">
    <h2 style="text-align:left">Campaign Purpose</h2>
    <div class="purpose-row">
      <p>Our campaign exists to help every child in the country enjoy more time to play. Busy lives and screens can crowd out simple fun, so we give parents easy ideas that fit into any day. From a walk to the shops to a rainy afternoon indoors, there is always a moment for a game. We work with schools, clubs and local groups to spread the word, and we share stories from families who have made play part of daily life. Every small moment counts, and together we can make childhood brighter.<br><br><a class="read-more" href="#">Read More »</a></p>
      <div class="purpose-photo" role="img" aria-label="Photo of a parent and child playing together"></div>
    </div>
  </div>
</section>

<footer class="site-footer">
  <div class="app">
    <h4>PLAY APP</h4>
    <a class="store" href="#"><small>Download for</small><strong>Phones</strong></a>
    <a class="store" href="#"><small>Available for</small><strong>Tablets</strong></a>
  </div>
  <div class="guild">
    <div class="name"><i></i>Northern Games &amp; Crafts Guild</div>
    <p>12 Meadowbank Lane, Leeds, LS6 2QT<br>Click here to read the disclaimer<br>© 2014 Northern Games &amp; Crafts Guild Ltd. All Rights Reserved.</p>
  </div>
  <div class="footer-art" role="img" aria-label="Cartoon characters of children waving"></div>
</footer>

</body>
</html>
```